Tabloid Magazine Flyer Class Action Lawsuit

Create a bold, 2-page 8.5" x 11" flyer with the look and feel of a tabloid exposé — loud, sensational, and impossible to ignore. Use bold fonts, dramatic headlines, and high-contrast colors (red, black, white, deep blue). Fill every inch of space — no white space, no subtlety. Use the provided images prominently. Page 1 should grab attention with a shocking headline, impactful image, and strong call to action. Page 2 should stack bold subheadings and explosive bullet points. Emphasize urgency, outrage, and grassroots power. This flyer is meant to rally a community.
Updates

Need to extend because we haven't received a design that meets our needs

Target Market(s)

All instructions and content are in the attached word doc

Industry/Entity Type

Requirements
Must have
• All instructions and content are in the attached word doc
Nice to have
Should not have

```html
<!DOCTYPE html>
<html lang="en">
<head>
<meta charset="utf-8">
<title>Harbor Point Park Exposed – Flyer</title>
<link rel="stylesheet" href="https://fonts.googleapis.com/css2?family=Anton&family=Montserrat:wght@400;500;700;800;900&display=swap">
<style>
  :root{
    --navy:#14145e;
    --navy-deep:#10104f;
    --red:#d10a0f;
    --blue:#1a6fd1;
    --sky:#6fb8f0;
    --white:#ffffff;
    --stage:#bcbcbc;
  }
  *{box-sizing:border-box;margin:0;padding:0}
  html,body{width:957px;height:1200px;overflow:hidden;background:var(--stage)}
  body{font-family:"Montserrat",sans-serif;color:var(--white)}
  .spread{position:absolute;top:302px;left:12px;display:flex;gap:13px}
  .page{position:relative;width:460px;height:595px;background:var(--navy);overflow:hidden}
  .page::after{content:"";position:absolute;left:0;right:0;bottom:0;height:6px;background:var(--blue)}
  .url{position:absolute;left:0;right:0;text-align:center;font-weight:900;color:var(--white);letter-spacing:.2px}

  /* page one */
  .masthead{position:absolute;top:13px;left:0;right:0;height:128px;background:var(--red);text-align:center;padding-top:20px}
  .masthead h1{font-family:"Anton",sans-serif;font-weight:400;font-size:38px;line-height:1;letter-spacing:.5px}
  .masthead .deck{margin-top:10px;font-weight:900;font-size:16px;line-height:1.2}
  .rally{position:absolute;top:150px;left:0;right:0;height:86px}
  .rally .fight{position:absolute;left:35px;top:0;width:122px;height:86px;font-weight:900;font-size:13.5px;line-height:1.2;padding-top:6px}
  .rally .divider{position:absolute;left:157px;top:0;width:1px;height:86px;background:#8a8ac0}
  .rally .divider::after{content:"";position:absolute;left:0;bottom:0;width:303px;height:1px;background:#8a8ac0}
  .rally .claim{position:absolute;left:176px;top:12px;color:var(--sky);font-weight:900;font-size:12.3px;line-height:1.55}
  .join{position:absolute;top:243px;left:29px;font-weight:900;font-size:15.2px;line-height:1.18}
  .tile{position:absolute;left:30px;width:127px;text-align:center;font-weight:800}
  .tile-place{top:290px;height:76px;background:var(--red);font-size:9.5px;line-height:1.3;padding-top:11px}
  .tile-save{top:377px;height:73px;background:var(--blue);padding-top:6px;line-height:1}
  .tile-save small{display:block;font-size:7.6px;font-weight:800}
  .tile-save strong{display:block;font-weight:900;font-size:16.5px;line-height:1.02}
  .tile-families{top:463px;height:73px;background:var(--red);font-size:11px;line-height:1.18;padding-top:7px;font-weight:700}
  .tile-families b{font-weight:900}
  .lawsuit{position:absolute;left:172px;top:291px;width:270px}
  .lawsuit h2{color:var(--sky);font-weight:900;font-size:17.5px;line-height:1.18}
  .lawsuit p{font-weight:500;font-size:10.7px;line-height:1.3;margin-top:14px}
  .gallery{position:absolute;left:172px;top:467px;display:flex;gap:9px}
  .gallery .photo{width:81px;height:71px;border:2px solid var(--white)}
  .photo-book{background:linear-gradient(135deg,#3f6aa8,#8c6a3a)}
  .photo-tower{background:linear-gradient(180deg,#3a6ea8,#e8a35a 55%,#6a5a4a)}
  .photo-units{background:linear-gradient(180deg,#9fc4e2,#4d86b3 60%,#3e5f7a)}
  .page-one .url{top:552px;font-size:25.5px}

  /* page two */
  .exposed-bar{position:absolute;top:10px;left:0;right:0;height:47px;background:var(--red);padding:6px 14px 0;font-size:7.1px;line-height:1.22;font-weight:600}
  .exposed-bar b{font-weight:900}
  .headline{position:absolute;top:66px;left:14px;color:var(--sky);font-weight:900;font-size:16.4px;letter-spacing:.2px}
  .column{position:absolute;top:96px}
  .col-left{left:12px;width:216px}
  .col-right{left:226px;width:225px}
  .point{position:relative;padding-left:36px;margin-bottom:9px}
  .point .icon{position:absolute;left:0;top:0;width:24px;height:24px}
  .point h3{color:var(--sky);font-weight:900;font-size:9.3px;line-height:1.18}
  .point p{font-weight:500;font-size:7.2px;line-height:1.22}
  .col-right .point p.large{font-size:8.4px;line-height:1.24}
  .evidence{position:absolute;left:245px;top:438px;width:168px;height:98px}
  .evidence .photo{width:168px;height:64px;background:linear-gradient(180deg,#5a4a3e,#a47a4e 60%,#3a2a20)}
  .evidence .badges{height:34px;background:var(--white);display:flex;align-items:center;justify-content:space-around;padding:0 8px}
  .badge-wide{width:52px;height:20px;background:var(--red);border-radius:2px}
  .badge-octagon{width:22px;height:22px}
  .badge-square{width:26px;height:22px;background:var(--blue)}
  .support{position:absolute;left:12px;top:492px;font-size:8.4px;line-height:1.25;color:var(--sky);font-weight:700}
  .support strong{display:block;font-weight:900;font-size:11.6px}
  .support span{font-weight:500}
  .page-two .url{top:556px;font-size:25.5px;padding-left:10px}
</style>
</head>
<body>
<svg width="0" height="0" style="position:absolute" aria-hidden="true">
  <defs>
    <linearGradient id="icon-fill" x1="0" y1="0" x2="1" y2="1">
      <stop offset="0" stop-color="#b46bd6"/>
      <stop offset="1" stop-color="#2c5fd6"/>
    </linearGradient>
  </defs>
</svg>

<main class="spread">
  <!-- PAGE ONE -->
  <section class="page page-one">
    <header class="masthead">
      <h1>HARBOR POINT PARK EXPOSED</h1>
      <p class="deck">DISABLED CHILD TRAUMATIZED PUBLIC<br>LAND ABUSED FOR PROFIT</p>
    </header>

    <div class="rally">
      <p class="fight">HELP OUR<br>BEACH<br>COMMUNITY<br>FIGHT BACK</p>
      <span class="divider"></span>
      <p class="claim">HARBOR POINT PARK IS NOT PRIVATE.<br>IT IS PUBLIC PROPERTY OWNED<br>BY THE CITY, PAID FOR BY YOU.</p>
    </div>

    <p class="join">JOIN US &amp; SHOW YOUR SUPPORT @<br>SEACLIFF BEACH TOWN COUNCIL MEETING</p>

    <div class="tile tile-place">PLACE: HARBOR POINT PARK COMMUNITY ROOM (ABOVE THE ARCADE)</div>
    <div class="tile tile-save"><small>HELP OUR COMMUNITY</small><strong>SAVE<br>HARBOR POINT<br>PARK</strong></div>
    <div class="tile tile-families"><b>HARBOR POINT PARK</b><br>WAS BUILT FOR FAMILIES - NOT RAVES</div>

    <div class="lawsuit">
      <h2>CLASS ACTION LAWSUIT<br>FORMING NOW!</h2>
      <p>IF YOU’VE BEEN IMPACTED BY NOISE, DENIED PUBLIC ACCESS, OR HARMED BY THESE VIOLATIONS, YOU MAY BE ELIGIBLE FOR COMPENSATION.</p>
      <p style="margin-top:10px">WE’RE GATHERING STORIES AND PREPARING LEGAL ACTION.</p>
    </div>

    <div class="gallery">
      <div class="photo photo-book" role="img" aria-label="Photo of a class action law book beside a gavel"></div>
      <div class="photo photo-tower" role="img" aria-label="Photo of a lifeguard tower on the beach at sunset"></div>
      <div class="photo photo-units" role="img" aria-label="Photo of a row of portable toilets in a parking lot"></div>
    </div>

    <p class="url">www.FixHarborPointPark.com</p>
  </section>

  <!-- PAGE TWO -->
  <section class="page page-two">
    <div class="exposed-bar"><b>EXPOSED:</b> Marco Vitale, CEO of Meridian Holdings Group LLC the leaseholder of Harbor Point Park, has drawn community outrage for profiting off public land while operating Harbor Point Park in ways many say violate its lease and damage our beach, our peace, and our environment- all from his luxury estate in Oakridge Estates.</div>

    <h2 class="headline">WHAT THEY DON’T WANT YOU TO KNOW:</h2>

    <div class="column col-left">
      <article class="point">
        <svg class="icon" viewBox="0 0 24 24"><circle cx="12" cy="12" r="12" fill="url(#icon-fill)"/><rect x="8" y="6" width="8" height="12" rx="1" fill="none" stroke="#fff" stroke-width="1.3"/><circle cx="12" cy="13.5" r="2" fill="none" stroke="#fff" stroke-width="1.2"/></svg>
        <h3>ILLEGAL RAVES – NO PERMITS.</h3>
        <p>Explosive concerts over 100 decibels, blasting Seacliff Beach with bass -multiple times per week. According to Public Records these events had NO PERMITS &amp; NO CITY APPROVAL.</p>
      </article>
      <article class="point">
        <svg class="icon" viewBox="0 0 24 24"><circle cx="12" cy="12" r="12" fill="url(#icon-fill)"/><circle cx="12" cy="6.5" r="1.6" fill="#fff"/><path d="M12 9v5h3l1.5 4M9 11.5a4.5 4.5 0 1 0 5 5.5" fill="none" stroke="#fff" stroke-width="1.4"/></svg>
        <h3>DISABLED CHILD<br>TRAUMATIZED BY RAVE NOISE</h3>
        <p>A child with cerebral palsy and auditory sensitivity came to use the City’s Beach Accessibility Program but was over whelmed by deafening Rave noise and fled in distress. The illegal sound levels deny All individuals with similar disabilities access to public accommodations. This is a direct violation of the Americans with Disabilities Act.</p>
      </article>
      <article class="point">
        <svg class="icon" viewBox="0 0 24 24"><circle cx="12" cy="12" r="12" fill="url(#icon-fill)"/><rect x="7.5" y="6" width="9" height="12" rx="1" fill="none" stroke="#fff" stroke-width="1.3"/><path d="M9.5 9.5h5M9.5 12h5M9.5 14.5h5" stroke="#fff" stroke-width="1"/></svg>
        <h3>DOCUMENTED RUN OFF AND SUSPECTED ENVIRONMENTAL DISASTER</h3>
        <p>Improperly Stored Chemicals, oils, and waste water spilling into storm drains. Parking lots are trashed, flooded, and neglected. Stormwater compliance appears to be ignored.</p>
      </article>
      <article class="point">
        <svg class="icon" viewBox="0 0 24 24"><circle cx="12" cy="12" r="12" fill="url(#icon-fill)"/><path d="M12 5v3M7 7l2 2M17 7l-2 2M5.5 12h3M15.5 12h3" stroke="#fff" stroke-width="1.3"/><circle cx="12" cy="14" r="2.5" fill="#fff"/></svg>
        <h3>HARBOR POINT PARK: ACCIDENT<br>WAITING TO HAPPEN?</h3>
        <p>From the Big Comet to the rides and walkways, safety appears ignored. The lease requires independent engineer inspections - yet no reports can be found. With what looks like hundreds of code violations, the entire park may be one broken bolt from disaster. Who’s protecting the public?</p>
      </article>
    </div>

    <div class="column col-right">
      <article class="point">
        <svg class="icon" viewBox="0 0 24 24"><circle cx="12" cy="12" r="12" fill="url(#icon-fill)"/><path d="M6 17h12M8 17v-6l4-3 4 3v6" fill="none" stroke="#fff" stroke-width="1.3"/><rect x="10.5" y="13" width="3" height="4" fill="#fff"/></svg>
        <h3>THE BEACH HOUSE ISN’T THEIRS<br>– IT’S YOURS.</h3>
        <p>Harbor Point Park is shutting down public space for 9 private Beach House raves through July. But July 5 is different -“Liberty Fest” is a full-park, alcohol-fueled rave that shuts out the public from taxpayer-owned land. These takeovers appear to violate their lease and Measure K, which protects YOUR beach for ALL-not just paying partiers.</p>
      </article>
      <article class="point">
        <svg class="icon" viewBox="0 0 24 24"><circle cx="12" cy="12" r="12" fill="url(#icon-fill)"/><path d="M12 7l4 2.5v5L12 17l-4-2.5v-5z" fill="none" stroke="#fff" stroke-width="1.3"/><path d="M12 12v5M8 9.5l4 2.5 4-2.5" stroke="#fff" stroke-width="1"/></svg>
        <h3>EXPOSED: IS HARBOR POINT RUNNING AN UNETHICAL SELF-DEALING SCHEME ?</h3>
        <p>Harbor Point Park’s General Manager, Glen Harper, is also CEO of Vanguard Guard Services -the very company hired by Harbor Point for “security” services. And who’s listed as corporate secretary? Carla Vitale, close relative of the leaseholder Marco Vitale. Is this Self-Dealing?</p>
      </article>
      <article class="point">
        <svg class="icon" viewBox="0 0 24 24"><circle cx="12" cy="12" r="12" fill="url(#icon-fill)"/><rect x="7" y="7" width="10" height="7" rx="1" fill="none" stroke="#fff" stroke-width="1.3"/><path d="M12 14v4M8 8l8 6" stroke="#fff" stroke-width="1.2"/></svg>
        <h3>EXPOSED: HARBOR POINT PARK’S ILLEGAL SIGNS MISLEAD<br>THE PUBLIC.</h3>
        <p class="large">They’re tricking the public into believing city-owned land is private, violating their lease which requires signage clearly stating the property is city-owned and open to all.</p>
      </article>
    </div>

    <figure class="evidence">
      <div class="photo" role="img" aria-label="Photo of a judge's gavel resting on an open law book"></div>
      <div class="badges">
        <span class="badge-wide"></span>
        <svg class="badge-octagon" viewBox="0 0 22 22"><polygon points="7,1 15,1 21,7 21,15 15,21 7,21 1,15 1,7" fill="#d10a0f"/></svg>
        <span class="badge-square"></span>
      </div>
    </figure>

    <p class="support">HELP OUR COMMUNITY<strong>SAVE HARBOR POINT PARK</strong><span>HARBOR POINT PARK WAS BUILT FOR FAMILIES -<br>NOT RAVES</span></p>

    <p class="url">www.FixHarborPointPark.com</p>
  </section>
</main>
</body>
</html>
```